Vantiqo custom business card design

Need a authentic, innovative business card design for a new mobile app business. I am uploading a few screen images from our app for you to view. I would like app design theme to match business card design. I can also send logo images.

```html
<!DOCTYPE html>
<html lang="en">
<head>
<meta charset="utf-8">
<title>Vantiqo Business Card</title>
<link href="https://fonts.googleapis.com/css2?family=Montserrat:wght@700;800&family=Open+Sans:wght@400;600&display=swap" rel="stylesheet">
<style>
  :root {
    --backdrop: #7b7b7b;
    --card-front: #ececec;
    --ink: #1e1e1e;
    --brand-purple: #62008c;
    --white: #ffffff;
    --rule: #9a9a9a;
  }
  html, body {
    margin: 0;
    padding: 0;
    width: 1200px;
    height: 1200px;
    overflow: hidden;
    background: var(--backdrop);
  }
  .canvas {
    position: relative;
    width: 1200px;
    height: 1200px;
  }
  .card {
    position: absolute;
    top: 310px;
    height: 594px;
    overflow: hidden;
  }
  .card-front {
    left: 234px;
    width: 364px;
    background: var(--card-front);
    color: var(--ink);
    font-family: "Open Sans", sans-serif;
    text-align: center;
  }
  .brand-dot {
    position: absolute;
    left: 112px;
    top: 72px;
    width: 140px;
    height: 140px;
    border-radius: 50%;
    background: var(--brand-purple);
  }
  .brand-name {
    position: absolute;
    left: 0;
    right: 0;
    top: 236px;
    margin: 0;
    font-family: "Montserrat", sans-serif;
    font-weight: 800;
    font-size: 42px;
    line-height: 48px;
    color: var(--ink);
  }
  .person-name {
    position: absolute;
    left: 0;
    right: 0;
    top: 344px;
    margin: 0;
    font-family: "Montserrat", sans-serif;
    font-weight: 700;
    font-size: 24px;
    line-height: 28px;
    color: var(--brand-purple);
  }
  .person-title {
    position: absolute;
    left: 0;
    right: 0;
    top: 368px;
    margin: 0;
    font-size: 17px;
    line-height: 21px;
  }
  .divider {
    position: absolute;
    left: 78px;
    width: 208px;
    height: 1px;
    background: var(--rule);
  }
  .divider-top { top: 396px; }
  .divider-bottom { top: 507px; }
  .contact-list {
    position: absolute;
    left: 0;
    right: 0;
    top: 406px;
    margin: 0;
    padding: 0;
    list-style: none;
    font-size: 17px;
    line-height: 21.5px;
  }
  .contact-label { color: var(--brand-purple); }
  .contact-web { color: var(--brand-purple); }
  .address {
    position: absolute;
    left: 0;
    right: 0;
    top: 514px;
    margin: 0;
    font-size: 17px;
    line-height: 21.5px;
    font-style: normal;
  }
  .card-back {
    left: 627px;
    width: 370px;
    background: var(--ink);
  }
  .back-shape {
    position: absolute;
    inset: 0;
  }
  .back-circle {
    position: absolute;
    left: 17px;
    top: 122px;
    width: 300px;
    height: 300px;
    border-radius: 50%;
    background: var(--white);
  }
  .back-brand {
    position: absolute;
    left: 0;
    right: 0;
    top: 448px;
    margin: 0;
    text-align: center;
    font-family: "Open Sans", sans-serif;
    font-weight: 600;
    font-size: 30px;
    line-height: 36px;
    color: var(--white);
  }
  .back-web {
    position: absolute;
    left: 0;
    right: 0;
    top: 530px;
    margin: 0;
    text-align: center;
    font-family: "Open Sans", sans-serif;
    font-weight: 600;
    font-size: 17px;
    line-height: 22px;
    color: var(--white);
  }
</style>
</head>
<body>
<main class="canvas">
  <section class="card card-front">
    <div class="brand-dot"></div>
    <h1 class="brand-name">Vantiqo</h1>
    <h2 class="person-name">MARCUS ELLERY</h2>
    <p class="person-title">Managing Director</p>
    <div class="divider divider-top"></div>
    <ul class="contact-list">
      <li><span class="contact-label">P:</span> 044-318 672 905</li>
      <li><span class="contact-label">M:</span> 044-318 672 917</li>
      <li><span class="contact-label">E:</span> hello@vantiqo.com</li>
      <li class="contact-web">www.vantiqoapp.com</li>
    </ul>
    <div class="divider divider-bottom"></div>
    <address class="address">48 Harbour Lane, Suite 6<br>Norland, 204518.</address>
  </section>

  <section class="card card-back">
    <svg class="back-shape" width="370" height="594" viewBox="0 0 370 594" aria-hidden="true">
      <polygon points="0,73 370,495 370,594 0,594" fill="var(--brand-purple)"/>
    </svg>
    <div class="back-circle"></div>
    <p class="back-brand">Vantiqo</p>
    <p class="back-web">www.vantiqoapp.com</p>
  </section>
</main>
</body>
</html>
```